Tech business card design

We need an amazing business card design for our new business 'Pexla' a marketing tech startup based in Sydney, Australia. We provide an online marketplace for businesses to search and buy advertising media, connect with service providers and learn more about marketing. We wish to communicate 'cool tech', reliability and professionalism and design based around our logo.

Target Market(s)

Business Owners

Contact Information for Business Card

Name
Position
Email Address
Website
Phone Number

Font styles to use
Other font styles liked:
• Avenir & Avenir Next

Colors

Designer to choose colors to be used in the design.

```html
<!DOCTYPE html>
<html lang="en">
<head>
<meta charset="utf-8">
<title>Pexla Business Card</title>
<link rel="stylesheet" href="https://fonts.googleapis.com/css2?family=Mulish:wght@400;600;900&display=swap">
<style>
  :root {
    --navy: #13133a;
    --blue: #1b6fc0;
    --paper: #ffffff;
    --backdrop: #e9ebec;
    --ink: #1a1a3d;
    --muted: #4a4a5e;
  }
  * { box-sizing: border-box; margin: 0; padding: 0; }
  html, body { width: 1200px; height: 900px; overflow: hidden; }
  body {
    background: var(--backdrop);
    font-family: "Mulish", "Avenir Next", sans-serif;
    color: var(--ink);
    position: relative;
  }
  .card {
    position: absolute;
    left: 320px;
    width: 560px;
    height: 320px;
    background: var(--paper);
    overflow: hidden;
    box-shadow: 0 6px 18px rgba(0,0,0,0.12);
  }
  .card--front { top: 110px; }
  .card--back { top: 470px; }
  .card__band { position: absolute; left: 0; top: 0; width: 560px; height: 320px; }
  .brand {
    position: absolute;
    font-weight: 900;
    color: var(--navy);
    letter-spacing: -1px;
    line-height: 1;
  }
  .card--front .brand { left: 262px; top: 112px; font-size: 76px; }
  .brand__url {
    position: absolute;
    left: 276px; top: 198px;
    font-size: 14px;
    color: var(--muted);
    letter-spacing: 0.3px;
  }
  .card--back .brand { left: 196px; top: 152px; font-size: 54px; }
  .contact { position: absolute; left: 370px; top: 76px; }
  .contact__name { font-size: 20px; font-weight: 400; color: var(--ink); }
  .contact__role { font-size: 11px; color: var(--muted); margin-top: 2px; margin-bottom: 14px; }
  .contact__line {
    display: flex; align-items: center; gap: 8px;
    font-size: 12.5px; color: var(--ink); margin-bottom: 7px;
  }
  .contact__icon { width: 12px; height: 12px; flex: none; }
</style>
</head>
<body>
  <section class="card card--front">
    <svg class="card__band" viewBox="0 0 560 320" aria-hidden="true">
      <polygon points="0,0 200,0 110,320 0,320" fill="var(--navy)"/>
      <polygon points="212,0 232,0 142,320 122,320" fill="var(--blue)"/>
    </svg>
    <div class="brand">Pexla</div>
    <div class="brand__url">www.pexlamedia.com.au</div>
  </section>

  <section class="card card--back">
    <svg class="card__band" viewBox="0 0 560 320" aria-hidden="true">
      <polygon points="0,0 160,0 80,320 0,320" fill="var(--navy)"/>
      <polygon points="172,0 192,0 112,320 92,320" fill="var(--blue)"/>
    </svg>
    <div class="brand">Pexla</div>
    <div class="contact">
      <div class="contact__name">Daniel Moss</div>
      <div class="contact__role">Founder | Director</div>
      <div class="contact__line">
        <svg class="contact__icon" viewBox="0 0 12 12"><rect x="3" y="0.5" width="6" height="11" rx="1.2" fill="none" stroke="var(--ink)" stroke-width="1.2"/><rect x="5" y="9" width="2" height="1" fill="var(--ink)"/></svg>
        <span>+61 (0)412 555 208</span>
      </div>
      <div class="contact__line">
        <svg class="contact__icon" viewBox="0 0 12 12"><rect x="0.5" y="2" width="11" height="8" fill="var(--ink)"/><path d="M0.5,2 L6,6.5 L11.5,2" fill="none" stroke="#fff" stroke-width="1"/></svg>
        <span>daniel@pexlamedia.com.au</span>
      </div>
      <div class="contact__line">
        <svg class="contact__icon" viewBox="0 0 12 12"><circle cx="6" cy="6" r="5.4" fill="none" stroke="var(--ink)" stroke-width="1.1"/><ellipse cx="6" cy="6" rx="2.3" ry="5.4" fill="none" stroke="var(--ink)" stroke-width="1"/><line x1="0.6" y1="6" x2="11.4" y2="6" stroke="var(--ink)" stroke-width="1"/></svg>
        <span>www.pexlamedia.com.au</span>
      </div>
    </div>
  </section>
</body>
</html>
```